Website for enterprise software start-up

We need a new Wordpress website. We are an early stage start-up focused on mobile video technology for cellular operators. The audience is strategy, marketing and customer acquisition execs from the operators.

The purpose of the site is to act as a sales brochure and capture leads. A demo app can be downloaded from the current site, want to put that behind a contact form.

Current website is at www.velmora.tv. Similar number of pages. Looking for a clean design template, with minimal customization. Blog will remain as is.

Want to be able to modify the copy via Wordpress. Reference designs I like: quandrix.com, briskfold7metrics.com

Target Market(s)

Mobile operators and MVNOs in the US and Asia Pacific regions

Industry/Entity Type

Business Software

Coding

Coded - Design and coding required

Number of Pages Required

4 page

Font styles to use
Sans Serif

Colors
f78f20

Requirements
Must have
• Form for downloading sample apps.
• Landing page with image, Product, Blog, About, Contact
• Team page

```html
<!DOCTYPE html>
<html lang="en">
<head>
<meta charset="utf-8">
<title>Velmora Media</title>
<link rel="stylesheet" href="https://fonts.googleapis.com/css2?family=Jost:wght@300;400;500;600;700&family=Open+Sans:wght@400;600;700&family=Merriweather:wght@400&display=swap">
<style>
:root{
  --orange:#f78f20;
  --orange-light:#fba548;
  --ink:#333333;
  --muted:#666666;
  --white:#ffffff;
  --grey-bg:#ececec;
  --features-bg:#efefef;
  --footer:#2b2b2b;
  --footer-base:#1e1e1e;
  --footer-text:#cfcfcf;
  --heading:'Jost',sans-serif;
  --body:'Open Sans',sans-serif;
}
*{margin:0;padding:0;box-sizing:border-box}
html,body{width:1200px;height:2853px;overflow:hidden}
body{position:relative;background:var(--white);font-family:var(--body);color:var(--ink)}
.abs{position:absolute}

/* header */
.site-header{position:absolute;left:0;top:0;width:1200px;height:101px;background:var(--white);border-top:3px solid var(--orange)}
.brand{position:absolute;display:flex;align-items:center;gap:12px;font-family:var(--heading);font-weight:600;color:var(--ink)}
.brand-mark{width:44px;height:44px;background:var(--orange)}
.site-header .brand{left:131px;top:24px;font-size:34px}
.main-nav a{position:absolute;top:38px;font-family:var(--body);font-size:12.5px;letter-spacing:.5px;color:var(--ink);text-decoration:none}
.main-nav a.active{color:var(--orange)}

/* hero */
.hero{position:absolute;left:0;top:101px;width:1200px;height:513px;background:linear-gradient(90deg,#141414 0%,#3a3632 40%,#5a554f 70%,#8a847c 100%)}
.hero-title{position:absolute;left:0;width:1200px;top:168px;text-align:center;font-family:var(--heading);font-weight:700;font-size:52px;line-height:66px;letter-spacing:2px;color:var(--white)}
.hero-title .accent{color:var(--orange)}
.hero-sub{position:absolute;left:0;width:1200px;top:325px;text-align:center;font-family:'Merriweather',serif;font-size:21px;color:#eeeeee}
.btn{position:absolute;display:flex;align-items:center;justify-content:center;background:var(--orange);color:var(--white);font-family:var(--heading);font-weight:600;letter-spacing:1px;border-radius:3px}
.hero .btn{left:525px;top:388px;width:150px;height:49px;font-size:17px}
.slider-arrow{position:absolute;width:24px;height:44px}
.hero-shadow{position:absolute;left:250px;top:604px;width:700px;height:40px;border-radius:50%;background:radial-gradient(ellipse at center,rgba(0,0,0,.18) 0%,rgba(0,0,0,0) 70%)}

/* about */
.about-device{position:absolute;left:141px;top:708px;width:310px;height:351px;border:3px solid #d6d6d6;border-bottom:none;border-radius:48px 48px 0 0;background:#f6f6f6}
.about-screen{position:absolute;left:18px;top:72px;width:268px;height:279px;background:linear-gradient(180deg,#ffffff 0%,#ffffff 28%,#6b4a3a 30%,#a57a5c 70%,#3a2a22 100%)}
.section-title{position:absolute;font-family:var(--heading);font-weight:300;font-size:36px;color:var(--orange);text-transform:uppercase}
.centered{left:0;width:1200px;text-align:center}
.about-title{left:512px;top:716px}
.about-copy{position:absolute;left:512px;top:776px;width:560px;font-size:11.5px;line-height:20px;color:var(--muted);text-align:justify}
.about-copy p+p{margin-top:18px}
.about .btn{left:512px;top:938px;width:104px;height:38px;font-size:10px}

/* features */
.features{position:absolute;left:0;top:1059px;width:1200px;height:468px;background:linear-gradient(90deg,#f3f3f3 0%,#e8e6e4 45%,#ecebea 100%)}
.feature-icon{position:absolute;width:68px;height:62px;background:var(--orange);border-radius:3px;display:flex;align-items:center;justify-content:center}
.feature-name{position:absolute;font-family:var(--heading);font-size:20px;color:var(--orange);text-transform:uppercase}
.feature-text{position:absolute;width:210px;font-size:10.5px;line-height:19px;color:#555;text-align:justify}

/* testimonials */
.testimonials{position:absolute;left:0;top:1527px;width:1200px;height:314px;background:linear-gradient(180deg,var(--orange-light) 0%,var(--orange) 100%)}
.testimonials .section-title{color:var(--white);top:74px}
.avatar{position:absolute;left:129px;top:122px;width:118px;height:118px;border-radius:50%;border:4px solid var(--white);background:linear-gradient(160deg,#c9a58a,#7b5d4c)}
.quote{position:absolute;left:272px;top:150px;width:786px;font-size:11.5px;line-height:22px;color:var(--white)}
.quote cite{display:block;margin-top:8px;font-style:italic;font-size:11px}

/* team */
.team-card{position:absolute;top:1993px;width:215px;height:238px;overflow:hidden}
.team-photo{position:absolute;inset:0;background:linear-gradient(180deg,#e6e4de 0%,#cfcac2 55%,#2f3540 100%)}
.team-band{position:absolute;left:0;bottom:0;width:100%;height:72px;background:rgba(40,40,40,.72);text-align:center;color:var(--white)}
.team-band strong{display:block;margin-top:18px;font-family:var(--heading);font-weight:600;font-size:16px;letter-spacing:1.5px}
.team-band span{display:block;font-size:9.5px;letter-spacing:1px;margin-top:2px}
.team-card.featured{box-shadow:0 6px 14px rgba(0,0,0,.35)}
.team-card.featured .team-overlay{position:absolute;inset:0;background:rgba(20,20,20,.55);text-align:center;color:var(--white)}
.team-overlay strong{display:block;margin-top:92px;font-family:var(--heading);font-weight:600;font-size:16px;letter-spacing:1.5px}
.team-overlay span{display:block;font-size:9.5px;letter-spacing:1px;margin-top:2px}
.team-social{display:flex;justify-content:center;gap:14px;margin-top:14px}
.team-social i{width:14px;height:14px;border-radius:50%;background:var(--white)}

/* partners */
.partners{position:absolute;left:0;top:2288px;width:1200px;height:283px;background:var(--grey-bg)}
.partner{position:absolute;top:129px;width:171px;height:94px;background:var(--white);border:1px solid #dcdcdc;display:flex;align-items:center;justify-content:center}
.partner i{width:100px;height:28px;background:#cfcfcf;border-radius:4px}

/* footer */
.site-footer{position:absolute;left:0;top:2571px;width:1200px;height:225px;background:var(--footer);color:var(--footer-text)}
.site-footer .brand{left:131px;top:46px;font-size:40px;color:#a9a9a9}
.site-footer .brand-mark{background:#8c8c8c;width:50px;height:50px}
.social{position:absolute;top:127px;width:26px;height:26px;border-radius:50%;background:#1b1b1b}
.social.primary{background:var(--orange)}
.footer-col{position:absolute;top:57px}
.footer-col h4{font-family:var(--body);font-weight:600;font-size:13px;letter-spacing:.5px;color:#e6e6e6;margin-bottom:14px}
.footer-col li{list-style:none;font-size:11px;line-height:19px}
.store-badge{position:absolute;top:88px;height:38px;background:#000;border:1px solid #6a6a6a;border-radius:5px}
.footer-base{position:absolute;left:0;top:2796px;width:1200px;height:57px;background:var(--footer-base);color:#bdbdbd;font-size:11px;text-align:center;line-height:57px}
</style>
</head>
<body>

<header class="site-header">
  <div class="brand"><span class="brand-mark"></span>Velmora Media</div>
  <nav class="main-nav">
    <a class="active" style="left:641px">PRODUCT</a>
    <a style="left:749px">CONTACT</a>
    <a style="left:860px">BLOG</a>
    <a style="left:945px">ABOUT</a>
    <a style="left:1031px">LOGIN</a>
  </nav>
</header>

<section class="hero" role="img" aria-label="Photo of a person holding a smartphone playing a video">
  <h1 class="hero-title"><span class="accent">HIGH QUALITY</span> MOBILE<br>ENGAGEMENT</h1>
  <p class="hero-sub">We engage mobile audiences with the right video content</p>
  <a class="btn">GET DEMO</a>
  <svg class="slider-arrow" style="left:131px;top:222px" viewBox="0 0 24 44"><path d="M20 4 L4 22 L20 40" fill="none" stroke="#fff" stroke-width="3"/></svg>
  <svg class="slider-arrow" style="left:1049px;top:222px" viewBox="0 0 24 44"><path d="M4 4 L20 22 L4 40" fill="none" stroke="#fff" stroke-width="3"/></svg>
</section>
<div class="hero-shadow"></div>

<section class="about">
  <div class="about-device"><div class="about-screen" role="img" aria-label="App screen showing a video trailer thumbnail"></div></div>
  <h2 class="section-title about-title">About Velmora Media</h2>
  <div class="about-copy">
    <p>Velmora Media exists because video consumption is trending away from TV towards mobile, and because mobile media is trending away from pull consumption towards push consumption - where each user is notified of personalized content at the perfect moment.</p>
    <p>We started Velmora Media to help media publishers navigate these trends, solving the technical challenges of delivering personalized and highest quality mobile video experiences, and seizing the economic opportunity of attracting premium brand advertising.</p>
  </div>
  <a class="btn">READ MORE</a>
</section>

<section class="features" role="img" aria-label="Faded photo of people watching videos on their phones">
  <h2 class="section-title centered" style="top:80px">Our Features</h2>

  <div class="feature-icon" style="left:133px;top:158px"><svg width="30" height="22" viewBox="0 0 30 22"><rect x="0" y="3" width="19" height="16" rx="2" fill="#fff"/><path d="M20 11 L30 3 V19 Z" fill="#fff"/></svg></div>
  <div class="feature-name" style="left:219px;top:154px">Beautiful HD</div>
  <p class="feature-text" style="left:219px;top:184px">Reach your mobile audience with beautiful HD thumbnails and in-notification videos.</p>

  <div class="feature-icon" style="left:458px;top:158px"><svg width="22" height="24" viewBox="0 0 22 24"><rect x="2" y="0" width="6" height="24" fill="#fff"/><rect x="14" y="0" width="6" height="24" fill="#fff"/></svg></div>
  <div class="feature-name" style="left:544px;top:154px">Video Playback</div>
  <p class="feature-text" style="left:544px;top:184px">Reach your mobile audience with beautiful HD thumbnails and in-notification videos.</p>

  <div class="feature-icon" style="left:782px;top:158px"><svg width="30" height="24" viewBox="0 0 30 24"><path d="M2 8 H9 L24 1 V23 L9 16 H2 Z" fill="#fff"/><rect x="6" y="16" width="5" height="7" fill="#fff"/></svg></div>
  <div class="feature-name" style="left:868px;top:154px">Monetize</div>
  <p class="feature-text" style="left:868px;top:184px">Reach your mobile audience with beautiful HD thumbnails and in-notification videos.</p>

  <div class="feature-icon" style="left:133px;top:303px"><svg width="16" height="28" viewBox="0 0 16 28"><rect x="1" y="1" width="14" height="26" rx="2" fill="none" stroke="#fff" stroke-width="2"/><circle cx="8" cy="23" r="1.5" fill="#fff"/></svg></div>
  <div class="feature-name" style="left:219px;top:299px">Guarantee</div>
  <p class="feature-text" style="left:219px;top:329px">Reach your mobile audience with beautiful HD thumbnails and in-notification videos.</p>

  <div class="feature-icon" style="left:458px;top:303px"><svg width="28" height="28" viewBox="0 0 28 28"><circle cx="14" cy="14" r="13" fill="#fff"/><path d="M11 8 L20 14 L11 20 Z" fill="#f78f20"/></svg></div>
  <div class="feature-name" style="left:544px;top:299px">Revealed</div>
  <p class="feature-text" style="left:544px;top:329px">Reach your mobile audience with beautiful HD thumbnails and in-notification videos.</p>

  <div class="feature-icon" style="left:782px;top:303px"><svg width="28" height="28" viewBox="0 0 28 28"><circle cx="14" cy="14" r="13" fill="#fff"/><path d="M7 9 Q12 6 14 11 Q10 15 12 19 Q8 18 7 13 Z M17 6 Q22 9 22 15 Q19 14 17 11 Z" fill="#f78f20"/></svg></div>
  <div class="feature-name" style="left:868px;top:299px">Notifications</div>
  <p class="feature-text" style="left:868px;top:329px">Reach your mobile audience with beautiful HD thumbnails and in-notification videos.</p>
</section>

<section class="testimonials">
  <h2 class="section-title centered">Testimonials</h2>
  <div class="avatar" role="img" aria-label="Portrait photo of the reviewer"></div>
  <blockquote class="quote">" Lorem ipsum dolor sit amet, consectetur adipiscing elit, sed do eiusmod tempor incididunt ut labore et dolore magna aliqua. Ut enim ad minim veniam, quis nostrud exercitation ullamco laboris nisi ut aliquip ex ea commodo consequat. "<cite>- John Doe -</cite></blockquote>
  <svg class="slider-arrow" style="left:92px;top:159px" viewBox="0 0 24 44"><path d="M18 10 L6 22 L18 34" fill="none" stroke="#fde0bd" stroke-width="2"/></svg>
  <svg class="slider-arrow" style="left:1088px;top:159px" viewBox="0 0 24 44"><path d="M6 10 L18 22 L6 34" fill="none" stroke="#fde0bd" stroke-width="2"/></svg>
</section>

<section class="team">
  <h2 class="section-title centered" style="top:1898px">Our Team</h2>
  <svg class="slider-arrow" style="left:90px;top:2083px" viewBox="0 0 24 44"><path d="M18 10 L6 22 L18 34" fill="none" stroke="#777" stroke-width="2"/></svg>
  <svg class="slider-arrow" style="left:1088px;top:2083px" viewBox="0 0 24 44"><path d="M6 10 L18 22 L6 34" fill="none" stroke="#777" stroke-width="2"/></svg>

  <div class="team-card featured" style="left:133px">
    <div class="team-photo" role="img" aria-label="Portrait photo of Reuben"></div>
    <div class="team-overlay"><strong>REUBEN_CTO</strong><span>CEO OF COMPANY</span><div class="team-social"><i></i><i></i><i></i></div></div>
  </div>
  <div class="team-card" style="left:375px">
    <div class="team-photo" role="img" aria-label="Portrait photo of Marcus"></div>
    <div class="team-band"><strong>MARCUS</strong><span>CEO OF COMPANY</span></div>
  </div>
  <div class="team-card" style="left:612px">
    <div class="team-photo" role="img" aria-label="Portrait photo of Terrence"></div>
    <div class="team-band"><strong>TERRENCE</strong><span>FINANCIAL ADVISOR</span></div>
  </div>
  <div class="team-card" style="left:852px">
    <div class="team-photo" role="img" aria-label="Portrait photo of Anselm"></div>
    <div class="team-band"><strong>ANSELM</strong><span>FINANCIAL ADVISOR</span></div>
  </div>
</section>

<section class="partners">
  <h2 class="section-title centered" style="top:40px">Our Partners</h2>
  <svg class="slider-arrow" style="left:90px;top:154px" viewBox="0 0 24 44"><path d="M18 10 L6 22 L18 34" fill="none" stroke="#777" stroke-width="2"/></svg>
  <svg class="slider-arrow" style="left:1088px;top:154px" viewBox="0 0 24 44"><path d="M6 10 L18 22 L6 34" fill="none" stroke="#777" stroke-width="2"/></svg>
  <div class="partner" style="left:133px"><i></i></div>
  <div class="partner" style="left:325px"><i></i></div>
  <div class="partner" style="left:515px"><i></i></div>
  <div class="partner" style="left:706px"><i></i></div>
  <div class="partner" style="left:896px"><i></i></div>
</section>

<footer class="site-footer">
  <div class="brand"><span class="brand-mark"></span>Velmora Media</div>
  <span class="social primary" style="left:133px"></span>
  <span class="social" style="left:168px"></span>
  <span class="social" style="left:202px"></span>
  <span class="social" style="left:236px"></span>
  <span class="social" style="left:270px"></span>

  <div class="footer-col" style="left:483px">
    <h4>SITEMAP</h4>
    <ul><li>Product</li><li>Contact</li><li>Blog</li><li>About</li><li>Login</li></ul>
  </div>
  <div class="footer-col" style="left:668px">
    <h4>COMPANY</h4>
    <ul><li>Customers</li><li>Resources</li><li>Company</li><li>Privacy Policy</li></ul>
  </div>
  <div class="footer-col" style="left:820px">
    <h4>DOWNLOAD APPS</h4>
  </div>
  <span class="store-badge" style="left:822px;width:119px"></span>
  <span class="store-badge" style="left:951px;width:116px"></span>
</footer>
<div class="footer-base">© 2016 Velmora Media, Inc. - Privacy Policy</div>

</body>
</html>
```